Teach English in China Website Redesign Needed

We recruit native English speakers from the US, UK, etc. who want to teach English as a foreign language in schools in China. Our target customer is college educated, age 22-28 and they love to travel. We prefer designs with bright colors and lots of photos. We want to keep all the text on our current homepage, BrightLanternPost.com. We are open to changing our logo. A competitor's page that we like is pinemeadowtutors.com because of their bright colors, photos and use of white space. We are happy to give you a dofollow link and design credit on our homepage. The use of included photos is optional. We need at least a home page design and a standard blog post design.
Target Market(s)
Our target customer is college educated, age 22-28 and they love to travel. Half of our customers are kindergarten teachers. Half of our customers are male.
Logo Text
Bright Lantern Post
Requirements
Must have
- Bright colors
Should not have
- Our homepage must not look crowded. Use white space effectively.

```html
<!DOCTYPE html>
<html lang="en">
<head>
<meta charset="utf-8">
<title>Bright Lantern Post — Teach English in China</title>
<link href="https://fonts.googleapis.com/css2?family=Lato:wght@300;400;700&display=swap" rel="stylesheet">
<style>
:root{
  --red:#e3141b;
  --ink:#2b2b2b;
  --muted:#555;
  --white:#fff;
  --page-bg:#dcdcdc;
  --footer:#1f1f1f;
  --footer-text:#bdbdbd;
}
*{box-sizing:border-box;margin:0;padding:0}
html,body{width:1200px;height:3197px;overflow:hidden}
body{background:var(--page-bg);font-family:'Lato',sans-serif;color:var(--ink)}
.page{position:absolute;left:98px;top:0;width:1004px;height:3197px;background:var(--white)}
.site-header{height:102px;display:flex;align-items:center;justify-content:space-between;padding:0 40px}
.brand{font-weight:700;font-size:24px;color:var(--red);display:flex;align-items:center;gap:10px}
.brand-dot{width:14px;height:14px;border-radius:50%;background:var(--red)}
.main-nav{display:flex;gap:32px;font-size:15px}
.main-nav a{color:var(--ink);text-decoration:none}
.main-nav a.active{color:var(--red)}
.hero{position:relative;height:478px;color:var(--white);text-align:center;
  background:
    radial-gradient(ellipse 30% 55% at 12% 30%,rgba(150,160,140,.85),transparent 70%),
    radial-gradient(ellipse 25% 60% at 88% 25%,rgba(140,150,130,.8),transparent 70%),
    radial-gradient(ellipse 22% 45% at 48% 70%,rgba(150,100,60,.7),transparent 70%),
    linear-gradient(180deg,#9aa69a 0%,#6f8a4e 30%,#5e9a2e 58%,#4f8a22 80%,#3d6e1a 100%)}
.hero-copy{position:absolute;top:140px;left:0;width:100%}
.hero h1{font-size:62px;font-weight:700;text-shadow:0 2px 6px rgba(0,0,0,.45)}
.hero p{font-size:19px;font-weight:700;margin:20px 0 30px;text-shadow:0 1px 4px rgba(0,0,0,.5)}
.btn-red{background:var(--red);color:var(--white);font-size:14px;font-weight:700;padding:12px 34px;text-decoration:none}
.slider-arrow{position:absolute;top:212px;width:34px;height:34px;border-radius:50%;background:#111;display:flex;align-items:center;justify-content:center}
.slider-arrow.prev{left:80px}.slider-arrow.next{right:80px}
.section-title{font-size:36px;font-weight:700;text-align:center;color:var(--ink)}
.jobs{padding-top:48px}
.job-grid{display:grid;grid-template-columns:repeat(3,298px);column-gap:25px;row-gap:36px;padding:38px 28px 0}
.job-photo{height:169px}
.job-location{color:var(--red);font-size:15px;text-align:center;margin-top:14px}
.job-title{font-size:20px;font-weight:400;text-align:center;line-height:1.3;margin-top:10px}
.band{position:absolute;left:0;width:1004px;display:flex;flex-direction:column;align-items:center;justify-content:center;color:var(--white);text-align:center}
.highlights{top:1360px;height:306px;
  background:
    radial-gradient(ellipse 18% 40% at 32% 35%,#ff6a2a,rgba(200,60,20,.6) 45%,transparent 75%),
    radial-gradient(ellipse 30% 45% at 80% 40%,rgba(150,200,60,.8),transparent 70%),
    radial-gradient(ellipse 25% 40% at 15% 55%,rgba(90,170,50,.7),transparent 70%),
    linear-gradient(180deg,#0d1b2e 0%,#1f3a1e 45%,#2e5a1c 70%,#e0a030 82%,#3a2a14 100%)}
.band h2{font-size:38px;font-weight:700;text-shadow:0 2px 6px rgba(0,0,0,.6)}
.band p{font-size:20px;line-height:1.35;margin:10px 0 22px;max-width:500px;text-shadow:0 1px 4px rgba(0,0,0,.7)}
.btn-outline{border:1px solid var(--white);color:var(--white);font-size:12px;font-weight:700;padding:12px 26px;text-decoration:none}
.testimonials{position:absolute;top:1712px;left:0;width:1004px}
.testimonial-grid{display:grid;grid-template-columns:repeat(4,240px);padding:40px 22px 0}
.testimonial{text-align:center;padding:0 12px}
.avatar{width:124px;height:124px;border-radius:50%;margin:0 auto 30px}
.quote{font-size:12px;line-height:1.75;color:var(--muted);text-align:justify;text-align-last:center}
.author{color:var(--red);font-size:15px;font-weight:700;margin-top:26px}
.apply{top:2199px;height:307px;
  background:
    radial-gradient(ellipse 40% 35% at 55% 20%,#ffd24a,rgba(230,160,30,.6) 50%,transparent 80%),
    radial-gradient(ellipse 35% 20% at 70% 78%,rgba(240,180,60,.8),transparent 70%),
    linear-gradient(180deg,#6a4a14 0%,#c88a1e 30%,#8a6a22 50%,#4a4a1e 70%,#2a2412 100%)}
.apply h2{font-size:36px}
.blog{position:absolute;top:2545px;left:0;width:1004px}
.blog-list{display:flex;padding:40px 0 0 26px}
.post{display:flex;width:488px;gap:14px}
.post-photo{width:256px;height:196px;flex:none}
.post-body{width:168px}
.post h3{color:var(--red);font-size:20px;font-weight:400;line-height:1.2}
.post p{font-size:13px;line-height:1.65;color:var(--muted);margin-top:12px}
.site-footer{position:absolute;top:2881px;left:0;width:1004px;height:316px;background:var(--footer);color:var(--footer-text)}
.footer-col{position:absolute;top:36px}
.footer-col h4{color:var(--white);font-size:20px;font-weight:700;margin-bottom:18px}
.footer-col li{list-style:none;font-size:12px;line-height:1.75}
.footer-col address{font-style:normal;font-size:12px;line-height:1.75}
.social{position:absolute;top:42px;left:833px;display:flex;gap:20px}
.social span{width:12px;height:12px;border-radius:50%;background:var(--footer-text)}
.copyright{position:absolute;bottom:30px;width:100%;text-align:center;font-size:12px}
</style>
</head>
<body>
<div class="page">
  <header class="site-header">
    <div class="brand"><span class="brand-dot"></span>Bright Lantern Post</div>
    <nav class="main-nav">
      <a class="active" href="#">Home</a><a href="#">Available Jobs</a><a href="#">Apply Online</a><a href="#">Blog</a><a href="#">FAQ</a><a href="#">Contact us</a>
    </nav>
  </header>

  <section class="hero" role="img" aria-label="Photo of green sandstone pillar mountains in mist">
    <div class="hero-copy">
      <h1>Teach English in China</h1>
      <p>Want to teach English in China?</p>
      <a class="btn-red" href="#">APPLY ONLINE</a>
    </div>
    <span class="slider-arrow prev"><svg width="12" height="12" viewBox="0 0 12 12"><path d="M8 1 3 6l5 5" stroke="#fff" stroke-width="2" fill="none"/></svg></span>
    <span class="slider-arrow next"><svg width="12" height="12" viewBox="0 0 12 12"><path d="M4 1l5 5-5 5" stroke="#fff" stroke-width="2" fill="none"/></svg></span>
  </section>

  <section class="jobs">
    <h2 class="section-title">Teaching Jobs in China</h2>
    <div class="job-grid">
      <article><div class="job-photo" role="img" aria-label="Photo of a bright school reception area" style="background:linear-gradient(180deg,#f4f8ea 0%,#d8ecc0 35%,#8fd04a 65%,#4fae2a 100%)"></div><div class="job-location">Chongqing, or Hefei</div><h3 class="job-title">Teach Students Ages 14 to Adult in Nanjing</h3></article>
      <article><div class="job-photo" role="img" aria-label="Photo of a city skyline across a river" style="background:linear-gradient(180deg,#6fa0e0 0%,#a9c6ea 35%,#7e8a70 55%,#4a6a8a 75%,#3a4a3a 100%)"></div><div class="job-location">Chongqing, or Hefei</div><h3 class="job-title">Teach Students Ages 14 to Adult in Nanjing</h3></article>
      <article><div class="job-photo" role="img" aria-label="Photo of young children at a classroom table" style="background:linear-gradient(135deg,#e8c8a0 0%,#f08a5a 35%,#5aa0e0 65%,#f0e0c0 100%)"></div><div class="job-location">Chongqing, or Hefei</div><h3 class="job-title">Teach Students Ages 14 to Adult in Nanjing</h3></article>
      <article><div class="job-photo" role="img" aria-label="Photo of students writing at their desks" style="background:linear-gradient(135deg,#3a3a44 0%,#b8382e 40%,#e8e4de 60%,#2a2a30 100%)"></div><div class="job-location">Chongqing, or Hefei</div><h3 class="job-title">Teach Students Ages 14 to Adult in Nanjing</h3></article>
      <article><div class="job-photo" role="img" aria-label="Photo of a busy classroom with pupils at long tables" style="background:linear-gradient(135deg,#d8a060 0%,#c84a3a 35%,#f0d8a8 60%,#8a6040 100%)"></div><div class="job-location">Chongqing, or Hefei</div><h3 class="job-title">Teach Students Ages 14 to Adult in Nanjing</h3></article>
      <article><div class="job-photo" role="img" aria-label="Photo of city towers under a blue sky" style="background:linear-gradient(180deg,#1e5ac8 0%,#5a94e0 30%,#e8f0fa 55%,#b0b8c0 75%,#5a7a4a 100%)"></div><div class="job-location">Chongqing, or Hefei</div><h3 class="job-title">Teach Students Ages 14 to Adult in Nanjing</h3></article>
    </div>
  </section>

  <section class="band highlights" role="img" aria-label="Photo of a lit red pagoda beside a lake at night">
    <h2>Highlights</h2>
    <p>Competitive compensation: 7000-9000 RMB/month, up to 18,000 RMB.</p>
    <a class="btn-outline" href="#">READ MORE</a>
  </section>

  <section class="testimonials">
    <h2 class="section-title">Testimonials</h2>
    <div class="testimonial-grid">
      <div class="testimonial"><div class="avatar" role="img" aria-label="Portrait photo of a teacher" style="background:radial-gradient(circle at 50% 45%,#e8b080,#c07a4a 45%,#1a1a1a 75%)"></div><p class="quote">" Marisol was extremely helpful during the entire process. Moving to another country is a very challenging ordeal and having someone like Marisol on your side makes all the difference. She's continued to be incredibly helpful even after arriving. "</p><div class="author">Theo Vance</div></div>
      <div class="testimonial"><div class="avatar" role="img" aria-label="Portrait photo of a teacher" style="background:radial-gradient(circle at 50% 50%,#f0e4d8,#8a8a8a 55%,#2a2a2a 85%)"></div><p class="quote">" Marisol was extremely helpful during the entire process. Moving to another country is a very challenging ordeal and having someone like Marisol on your side makes all the difference. She's continued to be incredibly helpful even after arriving. "</p><div class="author">Priya Castellan</div></div>
      <div class="testimonial"><div class="avatar" role="img" aria-label="Photo of a teacher in a classroom" style="background:linear-gradient(160deg,#f4ece0 0%,#d89a6a 45%,#8a4a3a 75%,#5a6a8a 100%)"></div><p class="quote">" Marisol was extremely helpful during the entire process. Moving to another country is a very challenging ordeal and having someone like Marisol on your side makes all the difference. She's continued to be incredibly helpful even after arriving. "</p><div class="author">Wren Halvorsen</div></div>
      <div class="testimonial"><div class="avatar" role="img" aria-label="Portrait photo of a teacher" style="background:linear-gradient(160deg,#d83a3a 0%,#f0d0b0 45%,#6a3a2a 75%,#3a2a2a 100%)"></div><p class="quote">" Marisol was extremely helpful during the entire process. Moving to another country is a very challenging ordeal and having someone like Marisol on your side makes all the difference. She's continued to be incredibly helpful even after arriving. "</p><div class="author">Priya Castellan</div></div>
    </div>
  </section>

  <section class="band apply" role="img" aria-label="Photo of a river winding through karst hills at sunset">
    <h2>Apply Now</h2>
    <p>Please make sure you read our FAQ before submitting your information.</p>
    <a class="btn-outline" href="#">APPLY NOW</a>
  </section>

  <section class="blog">
    <h2 class="section-title">Recent Blog</h2>
    <div class="blog-list">
      <article class="post"><div class="post-photo" role="img" aria-label="Photo of the Great Wall in autumn" style="background:linear-gradient(180deg,#3a80e0 0%,#9ac4f0 30%,#e86a2a 48%,#b88a5a 65%,#6a5038 100%)"></div><div class="post-body"><h3>Basic Chinese Greetings</h3><p>Chinese is a pretty difficult language for English speakers to learn compared to Spanish or French. However, if you're going to China, take the time to learn some basics</p></div></article>
      <article class="post"><div class="post-photo" role="img" aria-label="Photo of schoolchildren in uniform standing in rows" style="background:linear-gradient(180deg,#c8c8c8 0%,#f4f4f4 30%,#d8283a 50%,#2a2a4a 72%,#c8c0b0 100%)"></div><div class="post-body"><h3>Rowan's ESL Corner for the Best TEFL</h3><p>Chinese is a pretty difficult language for English speakers to learn compared to Spanish or French. However, if you're going to China, take the time to learn some basics</p></div></article>
    </div>
  </section>

  <footer class="site-footer">
    <div class="footer-col" style="left:32px"><h4>Quick Links</h4><ul><li>Home</li><li>Available Jobs</li><li>Apply Online</li><li>Blog</li><li>FAQ</li></ul></div>
    <div class="footer-col" style="left:281px"><h4>Contact us</h4><address>2218 Heron Hollow Ln<br>Brookfield,<br>Ohio 44403<br><br>555-318-2046<br>marisol@brightlanternpost.com</address></div>
    <div class="footer-col" style="left:607px"><h4>Resources</h4><ul><li>FAQ</li><li>Hire a teacher</li><li>About Us</li><li>Contact Us</li></ul></div>
    <div class="social" aria-label="Social links"><span></span><span></span><span></span><span></span></div>
    <div class="copyright">2017 © brightlanternpost.com</div>
  </footer>
</div>
</body>
</html>
```